Webdesign Metall- und Stahlbau Verhoelt GmbH
Zielgruppe
Metall- und Stahlbau Verhoelt GmbH
Zielgruppe: öffentlicher Bereich, Industrie, Gesundheitswesen > deutschlandweit tätig
Aufgabenstellung
keine bewegten Bilder oder Elemente in der Website
klassisches Layout
sehr konservativ

```html
<!DOCTYPE html>
<html lang="de">
<head>
<meta charset="utf-8">
<title>Metall- und Stahlbau Verhoelt GmbH</title>
<link href="https://fonts.googleapis.com/css2?family=Poppins:wght@400;500;600;700;800&display=swap" rel="stylesheet">
<style>
:root{
  --blue:#0a0ad2;
  --yellow:#f6c733;
  --dark:#121212;
  --card:#262626;
  --light:#f4f4f4;
  --text:#222;
  --white:#fff;
}
*{margin:0;padding:0;box-sizing:border-box}
html,body{width:1200px;height:3932px;overflow:hidden}
body{font-family:'Poppins',sans-serif;color:var(--text);background:var(--white);position:relative}
.btn{position:absolute;display:flex;align-items:center;justify-content:center;font-size:12px;font-weight:600;text-decoration:none}
.btn-blue{background:var(--blue);color:var(--white)}
.btn-yellow{background:var(--yellow);color:#111}
.btn-grey{background:#444;color:var(--white)}
.btn-outline{border:1.5px solid #ddd;color:var(--white)}
.photo{position:absolute}
p{font-size:11.5px;line-height:17px}

.hero{position:absolute;left:0;top:0;width:1200px;height:606px}
.hero-shade{position:absolute;inset:0;background:linear-gradient(90deg,rgba(0,0,0,.55) 0%,rgba(0,0,0,.15) 60%,rgba(0,0,0,0) 100%)}
.brand{position:absolute;color:var(--white);font-weight:600}
.nav{position:absolute;left:402px;top:38px;display:flex;gap:26px}
.nav a{color:var(--white);font-size:12px;text-decoration:none}
.hero h1{position:absolute;left:125px;top:302px;width:600px;color:var(--white);font-size:38px;line-height:45px;font-weight:800;letter-spacing:-1.2px}
.hero p{position:absolute;left:125px;top:446px;width:560px;color:var(--white);font-size:11.5px;line-height:17px}

.about h2{position:absolute;left:632px;top:698px;width:420px;font-size:39px;line-height:45px;font-weight:800;letter-spacing:-1px}
.about p{position:absolute;left:632px;top:848px;width:430px;font-size:11.3px}

.dark{position:absolute;left:0;width:1200px;background:linear-gradient(135deg,#0e0e0e,#1c1c1c 50%,#0e0e0e)}
.section-title{position:absolute;left:0;width:1200px;text-align:center;font-weight:800;font-size:37px;letter-spacing:-1px}
.dark .section-title{color:var(--white)}
.svc{position:absolute;top:1336px;width:224px;height:344px;background:var(--card);color:var(--white)}
.svc h3{font-size:16px;font-weight:600;line-height:23px}
.svc p{font-size:11px;line-height:15px;margin-top:6px}
.svc .txt{position:absolute;left:22px;width:190px}

.branch{position:absolute;top:1897px;width:307px;height:113px;background:var(--light);padding:26px 32px}
.branch h3{display:flex;align-items:center;gap:12px;font-size:17px;font-weight:600}
.tick{width:20px;height:20px;background:var(--yellow);display:flex;align-items:center;justify-content:center}
.branch p{font-size:11px;line-height:17px;margin-top:8px;color:#444}
.branch.active{background:var(--blue);color:var(--white)}
.branch.active p{color:#dfe0ff}

.career{position:absolute;left:125px;top:2097px;width:950px;height:374px;background:var(--light)}
.career h2{position:absolute;left:61px;top:45px;font-size:38px;line-height:42px;font-weight:800;letter-spacing:-1px}
.career p{position:absolute;left:61px;top:145px;width:340px;font-size:11px}

.news{position:absolute;top:2704px;width:307px;height:309px;background:var(--card);color:var(--white);padding:30px 32px}
.news .date{font-size:11px}
.news h3{font-size:17px;line-height:26px;font-weight:600;margin-top:10px}
.news p{font-size:11px;line-height:17px;margin-top:12px;color:#ddd}

.contact h2{position:absolute;left:125px;top:3230px;font-size:38px;line-height:42px;font-weight:800;letter-spacing:-1px}
.contact p{position:absolute;left:125px;top:3330px;width:380px;font-size:12px;color:#555}
.form{position:absolute;left:597px;top:3176px;width:470px;height:293px;background:var(--light)}
.field{position:absolute;background:var(--white);font-size:11.5px;padding:0 21px;display:flex;align-items:center;color:#222}

.footer{position:absolute;left:0;top:3558px;width:1200px;height:374px;background:linear-gradient(135deg,#0e0e0e,#1c1c1c 50%,#0e0e0e);color:var(--white)}
.footer h4{position:absolute;font-size:16px;font-weight:600}
.footer ul{position:absolute;list-style:none;font-size:11.5px;line-height:27px}
.social{position:absolute;top:3650px;width:30px;height:30px;background:var(--yellow)}
.legal{position:absolute;top:3903px;font-size:10px;color:#ddd}
</style>
</head>
<body>

<section class="hero">
  <div class="photo" role="img" aria-label="Industriehalle mit Vorplatz unter bewölktem Himmel" style="inset:0;background:linear-gradient(180deg,#454b55 0%,#6d737b 40%,#8a8d90 55%,#4a4b4c 75%,#2e2e2e 100%)"></div>
  <div class="hero-shade"></div>
  <div class="brand" style="left:125px;top:29px;font-size:15px;line-height:19px">Metall- und Stahlbau<br>Verhoelt GmbH</div>
  <nav class="nav">
    <a href="#">Startseite</a><a href="#">Unternehmen</a><a href="#">Leistungen</a><a href="#">Lohnarbeit</a><a href="#">Impressum</a><a href="#">Datenschutz</a>
  </nav>
  <a class="btn btn-blue" href="#" style="left:978px;top:32px;width:97px;height:31px">Kontakt</a>
  <h1>Zuverlässige Lösungen für<br>den Metall- und Stahlbau in<br>ganz Deutschland</h1>
  <p>Die Metall- Und Stahlbau Verhoelt GmbH Erbringt Hochwertige Stahl- Und Metallbauleistungen Für Öffentliche Einrichtungen, Industrieanlagen Und Gesundheitsprojekte.</p>
  <a class="btn btn-yellow" href="#" style="left:125px;top:498px;width:168px;height:29px">Leistungen Ansehen</a>
</section>

<section class="about">
  <div class="photo" role="img" aria-label="Blick in eine große Fertigungshalle mit Stahlträgern" style="left:125px;top:695px;width:466px;height:408px;background:linear-gradient(180deg,#8d9396,#5f6468 50%,#4a4b4c)"></div>
  <h2>Über die Metall- und Stahlbau Verhoelt GmbH</h2>
  <p>Die Metall- Und Stahlbau Verhoelt GmbH Ist Seit Über Drei Jahrzehnten Ein Zuverlässiger Partner Für Anspruchsvolle Stahl- Und Metallbauprojekte In Ganz Deutschland.<br>Mit Einem Erfahrenen Team Von Spezialisten Und Modernster Fertigungstechnik Realisieren Wir Projekte Für Öffentliche Auftraggeber, Die Industrie Sowie Das Gesundheitswesen. Unsere Stärke Liegt In Der Präzisen Planung, Fachgerechten Ausführung Und Termingerechten Montage Komplexer Konstruktionen.<br>Qualität, Zuverlässigkeit Und Langjährige Erfahrung Zeichnen Unsere Arbeit Aus. Wir Verstehen Uns Als Verlässlicher Partner, Der Höchste Technische Standards Mit Wirtschaftlichen Lösungen Verbindet.</p>
  <a class="btn btn-blue" href="#" style="left:632px;top:1058px;width:163px;height:32px">Entdecken Sie Mehr</a>
</section>

<section class="dark" style="top:1191px;height:553px">
  <h2 class="section-title" style="top:52px">Unsere Leistungen</h2>
</section>
<article class="svc" style="left:125px">
  <div class="photo" role="img" aria-label="Stahlgerüst eines Gebäudes" style="left:0;top:0;width:224px;height:197px;background:linear-gradient(180deg,#b8c2cc,#7d8792)"></div>
  <div class="txt" style="top:215px"><h3>Stahlbau</h3><p>Lorem Ipsum Dolor Sit Amet Viverra Porttitor Semper</p></div>
  <a class="btn btn-grey" href="#" style="left:22px;top:286px;width:151px;height:31px">Erfahren Sie Mehr</a>
</article>
<article class="svc" style="left:367px">
  <div class="txt" style="top:20px"><h3>Metallbau</h3><p>Lorem Ipsum Dolor Sit Amet Viverra Porttitor Semper</p></div>
  <a class="btn btn-blue" href="#" style="left:22px;top:88px;width:151px;height:31px">Erfahren Sie Mehr</a>
  <div class="photo" role="img" aria-label="Stahlhalle im Rohbau auf Baustelle" style="left:0;top:147px;width:224px;height:197px;background:linear-gradient(180deg,#8fb4dc,#9b8d7c 60%,#b9835d)"></div>
</article>
<article class="svc" style="left:609px">
  <div class="photo" role="img" aria-label="Montage eines Stahlbaus mit Kran" style="left:0;top:0;width:224px;height:197px;background:linear-gradient(180deg,#9fb0c0,#7a8691)"></div>
  <div class="txt" style="top:215px"><h3>Sonderkonstruktionen</h3><p>Lorem Ipsum Dolor Sit Amet Viverra Porttitor Semper</p></div>
  <a class="btn btn-grey" href="#" style="left:22px;top:286px;width:151px;height:31px">Erfahren Sie Mehr</a>
</article>
<article class="svc" style="left:851px">
  <div class="txt" style="top:20px"><h3>Montage &amp; Projektabwicklung</h3></div>
  <a class="btn btn-grey" href="#" style="left:22px;top:74px;width:151px;height:31px">Erfahren Sie Mehr</a>
  <div class="photo" role="img" aria-label="Handwerker beim Schleifen von Stahlteilen" style="left:0;top:147px;width:224px;height:197px;background:linear-gradient(135deg,#3c4a5a,#6b7280 50%,#8a4a3a)"></div>
</article>

<section class="branches">
  <h2 class="section-title" style="top:1820px">Branchen</h2>
  <div class="branch" style="left:125px"><h3><span class="tick"><svg width="12" height="10" viewBox="0 0 12 10"><path d="M1 5l3.5 3.5L11 1" stroke="#111" stroke-width="2" fill="none"/></svg></span>Öffentlicher Bereich</h3><p>Lorem Ipsum Dolor Sit Amet Consectetur In Bibendum Mauris Leo Mattis.</p></div>
  <div class="branch active" style="left:447px"><h3><span class="tick"><svg width="12" height="10" viewBox="0 0 12 10"><path d="M1 5l3.5 3.5L11 1" stroke="#111" stroke-width="2" fill="none"/></svg></span>Industrie</h3><p>Lorem Ipsum Dolor Sit Amet Consectetur In Bibendum Mauris Leo Mattis.</p></div>
  <div class="branch" style="left:768px"><h3><span class="tick"><svg width="12" height="10" viewBox="0 0 12 10"><path d="M1 5l3.5 3.5L11 1" stroke="#111" stroke-width="2" fill="none"/></svg></span>Gesundheitswesen</h3><p>Lorem Ipsum Dolor Sit Amet Consectetur In Bibendum Mauris Leo Mattis.</p></div>
</section>

<section class="career">
  <h2>Karriere bei<br>Verhoelt</h2>
  <p>Wir Suchen Qualifizierte Fachkräfte, Die Mit Uns Gemeinsam Anspruchsvolle Projekte Realisieren Möchten. Als Traditionsreiches Unternehmen Bieten Wir Sichere Arbeitsplätze, Moderne Ausstattung Und Vielfältige Entwicklungsmöglichkeiten.<br>Werden Sie Teil Unseres Erfahrenen Teams Und Gestalten Sie Mit Uns Die Zukunft Des Stahl- Und Metallbaus.</p>
  <a class="btn btn-blue" href="#" style="left:61px;top:287px;width:130px;height:31px">Offene Stellen</a>
  <div class="photo" role="img" aria-label="Stahlskelettbau bei Sonnenuntergang mit gelagerten Stahlprofilen" style="left:466px;top:10px;width:473px;height:300px;background:linear-gradient(180deg,#6f94c8 0%,#c9b89a 40%,#5a6068 70%,#8d949c 100%)"></div>
</section>

<section class="dark" style="top:2559px;height:529px">
  <h2 class="section-title" style="top:66px">Aktuelle Meldungen</h2>
</section>
<article class="news" style="left:125px">
  <div class="date">12. Januar 2026</div>
  <h3>Erfolgreicher Projektabschluss Verwaltungsgebäude München</h3>
  <p>Termingerechte Fertigstellung Der Stahlkonstruktion Für Das Neue Verwaltungsgebäude Im Münchner Stadtgebiet.</p>
  <a class="btn btn-outline" href="#" style="left:32px;top:245px;width:116px;height:32px">Mehr Lesen</a>
</article>
<article class="news" style="left:447px">
  <div class="date">12. Januar 2026</div>
  <h3>Zertifizierung Nach DIN EN 1090 Erfolgreich Erneuert</h3>
  <p>Lorem Ipsum Dolor Sit Amet Consectetur. Semper Cursus Lectus Vestibulum Quis Morbi Sagittis Cursus Amet. Cursus Non Volutpat Eleifend Dignissim In Aliquam. Varius Maecenas Egestas Sit Metus Nec Hendrerit Morbi Morbi Sed. Aliquet Erat Placerat Nullam.</p>
  <a class="btn btn-blue" href="#" style="left:32px;top:245px;width:116px;height:32px">Mehr Lesen</a>
</article>
<article class="news" style="left:768px">
  <div class="date">12. Januar 2026</div>
  <h3>Auftrag Für Klinikum-Erweiterung In Norddeutschland</h3>
  <p>Lorem Ipsum Dolor Sit Amet Consectetur. Morbi Fringilla Ut Sollicitudin Condimentum Urna Non Netus Et. Vestibulum Consequat Dolor Cursus Diam Mollis. Turpis Praesent Et.</p>
  <a class="btn btn-outline" href="#" style="left:32px;top:245px;width:116px;height:32px">Mehr Lesen</a>
</article>

<section class="contact">
  <h2>Nehmen Sie<br>Kontakt auf</h2>
  <p>Lorem ipsum dolor sit amet consectetur. Arcu neque porttitor mattis commodo phasellus ut. At aliquet arcu tincidunt est consequat scelerisque arcu. Arcu euismod quam sit sit dignissim fermentum adipiscing. Sagittis donec.</p>
  <div class="form">
    <div class="field" style="left:20px;top:20px;width:209px;height:36px">Vorname</div>
    <div class="field" style="left:241px;top:20px;width:209px;height:36px">Nachname</div>
    <div class="field" style="left:20px;top:69px;width:209px;height:36px">E-Mail</div>
    <div class="field" style="left:241px;top:69px;width:209px;height:36px">Service</div>
    <div class="field" style="left:20px;top:119px;width:430px;height:114px;align-items:flex-start;padding-top:14px">Nachricht</div>
    <a class="btn btn-blue" href="#" style="left:20px;top:247px;width:142px;height:32px">Jetzt Einreichen</a>
  </div>
</section>

<footer class="footer">
  <div class="brand" style="left:125px;top:80px;font-size:19px;line-height:24px">Metall- und Stahlbau<br>Verhoelt GmbH</div>
  <p style="position:absolute;left:125px;top:140px;width:290px;font-size:11.5px">Lorem Ipsum Dolor Sit Amet Consectetur Tempus Vulputate In Ut Phasellus Nibh Orci.</p>
  <h4 style="left:483px;top:62px">Schnelle Links</h4>
  <ul style="left:483px;top:90px"><li>Startseite</li><li>Unternehmen</li><li>Leistungen</li><li>Lohnarbeit</li><li>Impressum</li><li>Datenschutz</li></ul>
  <h4 style="left:658px;top:62px">KONTAKT</h4>
  <ul style="left:660px;top:90px"><li>+49 (0) 341 908172-0</li><li>E-Mail: info@verhoelt-stahlbau.de</li></ul>
  <h4 style="left:940px;top:62px">FOLGEN SIE UNS</h4>
  <div style="position:absolute;left:125px;top:334px;width:950px;height:1px;background:#444"></div>
</footer>
<div class="social" style="left:941px"></div>
<div class="social" style="left:980px"></div>
<div class="social" style="left:1020px"></div>
<div class="legal" style="left:125px">© 2026 Metall- Und Stahlbau Verhoelt GmbH. Alle Rechte Vorbehalten.</div>
<div class="legal" style="left:909px">Impressum. Datenschutzerklärung</div>

</body>
</html>
```